Mental Health care Company in Washington DC

We are a new mental health care services provider in Washington DC. Please look at these sites.
https://brightwaterfamilysupport.com
https://www.quietharborinc.com
https://willowgate-dc.org/
https://www.tidepathdc.com
https://www.thelanternofdc.com

```html
<!DOCTYPE html>
<html lang="en">
<head>
<meta charset="utf-8">
<title>Contact Us – Lumen Path Services</title>
<link rel="stylesheet" href="https://fonts.googleapis.com/css2?family=Outfit:wght@300;400;500;600&family=Roboto:wght@400;700&display=swap">
<style>
:root{
  --aqua:#a3d9dd;
  --aqua-deep:#8fcfd3;
  --card:#e9fbfc;
  --orange:#f4a763;
  --navy:#0b1b3d;
  --ink:#2b2b2b;
  --body:#2f4650;
  --line:#c9c9c9;
  --white:#ffffff;
}
*{box-sizing:border-box;margin:0;padding:0}
html,body{width:705px;height:1200px;overflow:hidden;background:var(--white)}
body{position:relative;font-family:"Outfit",sans-serif;color:var(--ink)}
.abs{position:absolute}

/* top bar */
.topbar{left:0;top:0;width:705px;height:47px;background:var(--aqua)}
.call-icon{left:54px;top:13px;width:23px;height:23px;border:1px solid rgba(255,255,255,.8);border-radius:5px;display:flex;align-items:center;justify-content:center}
.call-label{left:80px;top:14px;font-size:6px;color:var(--white);font-weight:300}
.call-number{left:80px;top:20px;font-size:11px;color:var(--white);font-weight:400}
.nav{top:16px;font-size:8.5px;color:var(--white);font-weight:400}
.btn-appoint{left:538px;top:10px;width:123px;height:26px;border-radius:13px;background:var(--orange);color:var(--white);font-size:8.5px;display:flex;align-items:center;justify-content:center}

/* hero */
.hero{left:0;top:47px;width:705px;height:220px;border-radius:19px;overflow:hidden;background:#f3f5f7}
.hero-left{left:0;top:0;width:236px;height:220px;background:linear-gradient(90deg,#f7f8fa,#eef1f4)}
.hero-photo{left:236px;top:0;width:469px;height:220px;background:linear-gradient(100deg,#c9d3dc 0%,#7f98b8 30%,#b69a82 65%,#6b4a35 100%)}
.brand{left:49px;top:20px;font-size:26px;font-weight:500;color:var(--navy);letter-spacing:-.3px}
.hero-title{left:51px;top:116px;font-size:24px;font-weight:500;color:var(--ink)}

/* info cards */
.card{top:309px;width:171px;height:117px;background:var(--card);border-radius:8px;text-align:center}
.card-icon{position:absolute;left:62px;top:18px;width:47px;height:47px;border-radius:50%;background:var(--aqua);display:flex;align-items:center;justify-content:center}
.card-text{position:absolute;left:0;right:0;top:74px;font-family:"Roboto",sans-serif;font-size:7.3px;line-height:12px;color:#333}

/* form */
.form-title{left:0;width:705px;top:458px;text-align:center;font-size:23px;font-weight:500;color:#222}
.field{border:1px solid var(--line);border-radius:3px;font-family:"Roboto",sans-serif;font-size:6.8px;color:#777;padding-left:12px;display:flex;align-items:center}
.field.area{align-items:flex-start;padding-top:11px}
.btn-submit{left:300px;top:686px;width:113px;height:34px;background:#1e1e1e;color:var(--white);font-family:"Roboto",sans-serif;font-weight:700;font-size:10.5px;display:flex;align-items:center;justify-content:center;border-radius:2px}

/* footer */
.footer{left:0;top:764px;width:705px;height:401px;background:var(--aqua)}
.footer-brand{left:53px;top:790px;font-size:24px;font-weight:500;color:var(--white)}
.tagline{left:201px;top:801px;font-size:11.3px;color:var(--white);font-weight:400}
.social{top:799px;width:19.5px;height:19.5px;background:var(--orange);border-radius:3px}
.rule{height:1px;background:rgba(80,120,130,.35)}
.f-head{font-size:11.5px;font-weight:500;color:var(--white);line-height:16px}
.f-text{font-size:7.3px;color:var(--body)}
.f-strong{font-size:7.3px;color:var(--body);font-weight:600;line-height:10.5px}
.under{height:1px;background:rgba(60,100,110,.35);width:173px;left:60px}
.pill-submit{left:60px;top:987px;width:40px;height:17px;border-radius:9px;background:var(--orange);color:var(--white);font-size:7px;display:flex;align-items:center;justify-content:center}
.link{left:301px;font-size:7.5px;color:var(--body);display:flex;align-items:center;gap:4px}
.sched{left:61px;top:1021px;font-size:15.5px;font-weight:600;color:var(--white)}
.sched-text{left:61px;top:1050px;width:340px;font-size:7.3px;line-height:10.5px;color:var(--body)}
.btn-phone{left:460px;top:1013px;width:182px;height:38px;border-radius:19px;background:var(--orange);color:var(--white);font-size:16px;font-weight:600;display:flex;align-items:center;justify-content:center;gap:7px}
.disclaimer{left:62px;top:1108px;width:583px;text-align:center;font-size:6.2px;line-height:9.3px;color:var(--body)}
.bottombar{left:0;top:1165px;width:705px;height:35px;background:var(--navy)}
.copy{top:1179px;font-size:7.3px;color:var(--white)}
</style>
</head>
<body>

<!-- top bar -->
<header class="abs topbar"></header>
<div class="abs call-icon">
  <svg width="13" height="13" viewBox="0 0 24 24" fill="none" stroke="#fff" stroke-width="1.5"><path d="M5 3h4l2 5-2.5 1.5a11 11 0 0 0 6 6L16 13l5 2v4a2 2 0 0 1-2 2A16 16 0 0 1 3 5a2 2 0 0 1 2-2z"/></svg>
</div>
<div class="abs call-label">Call us today:</div>
<div class="abs call-number">555-014-2290</div>
<nav>
  <span class="abs nav" style="left:255px">Home</span>
  <span class="abs nav" style="left:305px">About</span>
  <span class="abs nav" style="left:357px">Services</span>
  <span class="abs nav" style="left:416px">Contact</span>
</nav>
<div class="abs btn-appoint">Make an Appointment</div>

<!-- hero -->
<section class="abs hero">
  <div class="abs hero-left"></div>
  <div class="abs hero-photo" role="img" aria-label="Photo of a smiling counsellor taking notes while talking with a client"></div>
  <div class="abs brand">Lumen Path</div>
  <h1 class="abs hero-title" style="font-weight:500">Contact Us</h1>
</section>

<!-- info cards -->
<div class="abs card" style="left:79px">
  <div class="card-icon">
    <svg width="24" height="24" viewBox="0 0 24 24" fill="none" stroke="#fff" stroke-width="1.2"><rect x="3" y="6" width="18" height="13" rx="1"/><path d="M3 7l9 7 9-7"/><circle cx="12" cy="9" r="2.5"/></svg>
  </div>
  <div class="card-text">info@lumenpathservices.com</div>
</div>
<div class="abs card" style="left:269px">
  <div class="card-icon">
    <svg width="22" height="22" viewBox="0 0 24 24" fill="none" stroke="#fff" stroke-width="1.2"><path d="M12 21s-6-6.5-6-11a6 6 0 0 1 12 0c0 4.5-6 11-6 11z"/><circle cx="12" cy="10" r="2.3"/><ellipse cx="12" cy="21" rx="5" ry="1.2"/></svg>
  </div>
  <div class="card-text">4410 Birchmont Avenue, Suite 210,<br>Washington, DC 20011</div>
</div>
<div class="abs card" style="left:458px">
  <div class="card-icon">
    <svg width="22" height="22" viewBox="0 0 24 24" fill="none" stroke="#fff" stroke-width="1.2"><path d="M5 3h4l2 5-2.5 1.5a11 11 0 0 0 6 6L16 13l5 2v4a2 2 0 0 1-2 2A16 16 0 0 1 3 5a2 2 0 0 1 2-2z"/><path d="M15 3a6 6 0 0 1 6 6M15 6.5a2.5 2.5 0 0 1 2.5 2.5"/></svg>
  </div>
  <div class="card-text">555-014-2290</div>
</div>

<!-- contact form -->
<h2 class="abs form-title">CONTACT FORM</h2>
<div class="abs field" style="left:98px;top:507px;width:252px;height:28px">Enter your First name</div>
<div class="abs field" style="left:360px;top:507px;width:252px;height:28px">Enter your Email</div>
<div class="abs field" style="left:98px;top:546px;width:252px;height:29px">Enter your Last name</div>
<div class="abs field" style="left:360px;top:546px;width:252px;height:29px">Enter your phone</div>
<div class="abs field area" style="left:98px;top:586px;width:514px;height:79px">Enter your message</div>
<div class="abs btn-submit">SUBMIT NOW</div>

<!-- footer -->
<footer class="abs footer"></footer>
<div class="abs footer-brand">Lumen Path</div>
<div class="abs tagline">Find out how we approach our client’s treatment and therapy !</div>
<div class="abs social" style="left:555px"></div>
<div class="abs social" style="left:579px"></div>
<div class="abs social" style="left:603px"></div>
<div class="abs social" style="left:627px"></div>
<div class="abs rule" style="left:54px;top:843px;width:592px"></div>

<div class="abs f-head" style="left:60px;top:876px">Sign Up for Our<br>Newsletter</div>
<div class="abs f-text" style="left:61px;top:921px">Enter Your Name</div>
<div class="abs under" style="top:939px"></div>
<div class="abs f-text" style="left:61px;top:956px">Enter Your Email</div>
<div class="abs under" style="top:974px"></div>
<div class="abs pill-submit">Submit</div>

<div class="abs f-head" style="left:298px;top:871px">Quick Links</div>
<div class="abs link" style="top:897px"><span>›</span>Home</div>
<div class="abs link" style="top:914px"><span>›</span>About</div>
<div class="abs link" style="top:931px"><span>›</span>Services</div>
<div class="abs link" style="top:948px"><span>›</span>Contact</div>

<div class="abs f-head" style="left:429px;top:872px">Get In Touch</div>
<svg class="abs" style="left:429px;top:902px" width="9" height="9" viewBox="0 0 24 24" fill="none" stroke="#2f4650" stroke-width="2"><path d="M5 3h4l2 5-2.5 1.5a11 11 0 0 0 6 6L16 13l5 2v4a2 2 0 0 1-2 2A16 16 0 0 1 3 5a2 2 0 0 1 2-2z"/></svg>
<div class="abs f-text" style="left:442px;top:902px">Call Us</div>
<div class="abs f-strong" style="left:429px;top:914px">555-014-2290</div>
<svg class="abs" style="left:540px;top:903px" width="9" height="9" viewBox="0 0 24 24" fill="none" stroke="#2f4650" stroke-width="2"><circle cx="12" cy="12" r="9"/><path d="M12 7v5l3 2"/></svg>
<div class="abs f-text" style="left:553px;top:903px">e-mail us</div>
<div class="abs f-strong" style="left:540px;top:915px">info@lumenpathservices.com</div>
<svg class="abs" style="left:429px;top:940px" width="9" height="9" viewBox="0 0 24 24" fill="none" stroke="#2f4650" stroke-width="2"><circle cx="12" cy="12" r="9"/><path d="M12 7v5l3 2"/></svg>
<div class="abs f-text" style="left:442px;top:940px">Location Hours</div>
<div class="abs f-strong" style="left:429px;top:952px">Mon – Fri: 9:00 – 6:00<br>Sat: 10 – 4:00</div>
<svg class="abs" style="left:538px;top:940px" width="9" height="10" viewBox="0 0 24 24" fill="none" stroke="#2f4650" stroke-width="2"><path d="M12 21s-6-6.5-6-11a6 6 0 0 1 12 0c0 4.5-6 11-6 11z"/><circle cx="12" cy="10" r="2.3"/></svg>
<div class="abs f-text" style="left:551px;top:941px">Address</div>
<div class="abs f-strong" style="left:538px;top:953px">4410 Birchmont Avenue, Suite 210,<br>Washington, DC 20011</div>

<div class="abs sched">Schedule Your Appointment</div>
<p class="abs sched-text">It is a long established fact that a reader will be distracted by the readable content of a page when looking at its layout. The point of using Lorem Ipsum is that it has a more-or-less normal.</p>
<div class="abs btn-phone">
  <svg width="17" height="17" viewBox="0 0 24 24" fill="none" stroke="#fff" stroke-width="2.2"><path d="M5 3h4l2 5-2.5 1.5a11 11 0 0 0 6 6L16 13l5 2v4a2 2 0 0 1-2 2A16 16 0 0 1 3 5a2 2 0 0 1 2-2z"/><path d="M15 3a6 6 0 0 1 6 6M15 6.5a2.5 2.5 0 0 1 2.5 2.5"/></svg>
  1-555-014-2290
</div>
<div class="abs rule" style="left:61px;top:1085px;width:582px"></div>
<p class="abs disclaimer">This website is for mental health care services purposes only.It is a long established fact that a reader will be distracted by the readable content of a page when looking at its layout. The point of using Lorem Ipsum is that it has a more-or-less normal distribution of letters, as opposed to using ‘Content here, content here’, making it look like readable English. Many desktop publishing packages and web page editors now use Lorem Ipsum as their default model text, and a search for ‘lorem ipsum’ will uncover many web sites still in their infancy.</p>

<div class="abs bottombar"></div>
<div class="abs copy" style="left:62px">Copyright © 2025 lumenpathservices.com</div>
<div class="abs copy" style="right:62px">Privacy Policy | Client Terms of Service</div>

</body>
</html>
```